BRTL web site redesign

Coastal Linkage Engineering service (BRTL) is a diverse technology company specialising in design and installation of fibre optics, network convergence and building services, for commercial clients in Australia, we required a new design of our website to attract new clients, generate sales leads, and provide information about our services to the market. The site and should have a new technology look and feel and be designed in word press. our branding colour is blue.

Target Market(s)

New developments, Construction organisations, Commercial end users, IT managers, Consultants.

Industry/Entity Type

It Company

Number of Pages Required

5+ page

Font styles to use
Sans Serif

Colors
0292cd
3176b5

Requirements
Must have
• key pages.
• Home page with some sizzle, automated pictures running through, I like the look of this competitor website http://www.gleamwirex.com.au/ good clean menus and easy to navigate.
• Services page our key services are Fibre optics, Security, Building services,Electrical. I would like the same page layout (Design) for all our services, with a find out more link on each page, manly picture driven with text around our key messaging.
• About us page with space for company profile and directors pictures, bio and contact information.
• Certifications / Accreditations page with have over 20 certifications on different products from suppliers, and a number of licences from governing bodies.
• Current and past projects page with case studies and customer outcomes
• Contact us page with options around what services they require more information on, please keep in mind the site is around generating sales Leeds and being seen as an industry expert.
Nice to have
• RSS feeds, Linked in link, to be placed within the design, Consistent BRTL branding,Same colour blue as our logo Document library for education information, white papers, presentations etc,
• a new technology look and feel, mobile friendly.
Should not have
• boring layout, move away from our cuurent website http://www.brtlgroup.com.au/
• no e eCommerce store required.

```html
<!DOCTYPE html>
<html lang="en">
<head>
<meta charset="utf-8">
<title>BRTL – Coastal Linkage Engineering service</title>
<link href="https://fonts.googleapis.com/css2?family=Open+Sans:wght@400;600;700;800&display=swap" rel="stylesheet">
<style>
:root{
  --blue:#0292cd;
  --blue-dark:#3176b5;
  --nav:#0a8fd0;
  --nav-active:#05639a;
  --ink:#333;
  --muted:#777;
  --light:#f1f1f1;
  --rule:#dcdcdc;
  --footer:#3f3f3f;
  --footer-deep:#262626;
  --accent-red:#d9302a;
  --accent-orange:#e0892b;
}
*{box-sizing:border-box;margin:0;padding:0}
html,body{width:1200px;height:2706px;overflow:hidden}
body{font-family:"Open Sans",Arial,sans-serif;color:var(--ink);background:#fff;position:relative;font-size:11px;line-height:1.5}
.abs{position:absolute}
a{color:inherit;text-decoration:none}
ul{list-style:none}

/* header */
.account-bar{right:165px;top:0;display:flex;gap:2px}
.account-bar a{background:#111;color:#fff;font-size:10px;font-weight:600;padding:7px 18px 8px;display:flex;align-items:center;gap:7px;letter-spacing:.3px}
.account-bar svg{width:12px;height:12px}
.brand{left:175px;top:34px;display:flex;align-items:center;gap:10px}
.brand-square{width:26px;height:26px;background:var(--blue)}
.brand-name{font-size:54px;font-weight:800;color:var(--blue);letter-spacing:1px;line-height:1}
.brand-tag{left:175px;top:96px;font-size:8px;color:var(--blue-dark);letter-spacing:.5px;text-transform:uppercase;font-weight:600}
.phone{left:555px;top:78px;display:flex;align-items:center;gap:10px;font-size:27px;font-weight:700;color:#1d2a38}
.search{left:810px;top:84px;width:220px;height:22px;border:1px solid #c8c8c8;display:flex;align-items:center;justify-content:space-between;padding:0 8px;color:#999;font-size:10px}

/* nav */
.main-nav{left:175px;top:127px;width:860px;height:34px;background:var(--nav);display:flex}
.main-nav a{color:#fff;font-size:13px;font-weight:600;text-transform:uppercase;display:flex;align-items:center;padding:0 24px;letter-spacing:.2px}
.main-nav a.is-active{background:var(--nav-active)}

/* slider */
.hero-band{left:0;top:161px;width:1200px;height:380px;background:linear-gradient(#e9e9e9,#d6d6d6)}
.hero{left:175px;top:169px;width:860px;height:356px;background:linear-gradient(120deg,#23404e 0%,#4d6470 35%,#2f3b44 60%,#8a9096 100%);overflow:hidden}
.hero-caption{left:0;top:222px;width:860px;height:90px;background:rgba(0,0,0,.35);padding:18px 20px;color:#fff;text-align:center}
.hero-caption h1{font-size:23px;font-weight:800;text-transform:uppercase;white-space:nowrap;line-height:1.3}
.hero-caption p{font-size:13px;margin-top:6px}
.hero-arrow{top:160px;width:26px;height:40px;background:rgba(0,0,0,.45);display:flex;align-items:center;justify-content:center}
.hero-dots{left:400px;top:334px;display:flex;gap:4px}
.hero-dots span{width:14px;height:14px;background:#bbb}
.hero-dots span.on{background:var(--accent-red)}

/* intro columns */
.intro{left:175px;top:557px;width:860px;display:grid;grid-template-columns:repeat(3,1fr);gap:28px}
.intro-col h2{display:flex;align-items:center;gap:14px;font-size:15px;font-weight:600;color:var(--blue);text-transform:uppercase;border-bottom:1px solid var(--rule);padding:0 0 8px 30px}
.intro-col p{font-size:11px;color:#555;margin-top:14px;padding-right:10px;line-height:1.6}
.service-list li{font-size:11.5px;color:#444;padding:9px 0;border-bottom:1px solid #eee}
.btn{display:inline-block;background:var(--blue-dark);color:#fff;font-size:9.5px;font-weight:600;padding:6px 16px;border-radius:3px}
.intro-btn{top:757px}

/* welcome */
.welcome{left:175px;top:852px;width:540px}
.welcome h2{font-size:30px;font-weight:400;color:#222}
.welcome h2 span{color:var(--blue);font-weight:600}
.welcome p{margin-top:12px;color:#555;line-height:1.6}
.welcome .more{display:block;text-align:right;color:var(--accent-orange);font-size:10px;margin-top:12px;font-weight:600}
.welcome-photo{left:755px;top:850px;width:265px;height:168px;background:linear-gradient(135deg,#b8d4e6,#5e84a2 60%,#2c3f55);box-shadow:0 1px 4px rgba(0,0,0,.3)}

/* highlight tabs */
.showcase{left:175px;top:1052px;width:860px;height:222px;background:var(--light);border:1px solid #e2e2e2}
.tabs{display:flex;height:46px;background:#fff}
.tabs span{width:135px;display:flex;align-items:center;justify-content:center;font-size:12px;font-weight:600;color:#444;background:#e6e6e6;border-right:1px solid #d3d3d3}
.tabs span.on{background:var(--blue);color:#fff}
.thumbs{display:flex;gap:21px;padding:30px 50px}
.thumb{width:110px;height:90px;border:3px solid #fff;box-shadow:0 1px 4px rgba(0,0,0,.25)}

/* about */
.about{left:175px;top:1300px;width:420px;text-align:right}
.about h2{font-size:24px;font-weight:400;text-align:center;color:#222;letter-spacing:.5px}
.about p{margin-top:10px;color:#555;line-height:1.5}
.about-btn{left:408px;top:1640px}
.news{left:625px;top:1305px;width:402px;height:368px;border:1px solid #d7d7d7;background:#fafafa}
.news h3{background:linear-gradient(var(--blue),var(--blue-dark));color:#fff;font-size:10.5px;font-weight:700;text-transform:uppercase;padding:7px 12px}
.news-item{display:flex;gap:12px;padding:11px 12px;border-bottom:1px solid #e3e3e3}
.news-thumb{flex:0 0 52px;height:46px;border:2px solid #fff;box-shadow:0 0 2px rgba(0,0,0,.3)}
.news-item b{display:block;color:var(--blue-dark);font-size:10px;font-weight:600}
.news-item em{display:block;font-style:normal;color:var(--blue);font-size:9.5px}
.news-item p{color:#666;font-size:9.5px;line-height:1.4}
.news .view-all{position:absolute;right:12px;bottom:8px;color:var(--accent-red);font-size:10px;font-weight:600}

/* partners */
.partners{left:0;top:1712px;width:1200px;text-align:center}
.partners h2{font-size:29px;font-weight:400;color:#222}
.partners p{color:#666;margin-top:6px}
.partner-row{display:flex;justify-content:center;gap:38px;margin-top:42px;align-items:center}
.partner-badge{width:125px;height:40px;background:#cfcfcf;border-radius:3px}
.partner-badge.round{width:56px;height:56px;border-radius:50%}

/* testimonials */
.reviews-title{left:190px;top:1968px;font-size:26px;font-weight:400;color:#222}
.reviews{left:190px;top:2030px;width:820px;display:grid;grid-template-columns:1fr 1fr;column-gap:60px;row-gap:34px}
.review{display:flex;gap:22px}
.avatar{flex:0 0 56px;height:56px;border-radius:50%;border:2px solid #e5e5e5;background:radial-gradient(circle at 50% 40%,#e7c7ad,#8a6a55)}
.review p{color:#555;line-height:1.5}
.review cite{display:block;font-style:normal;margin-top:10px;font-size:10px;color:#555}
.review cite b{color:var(--accent-red);font-weight:600}

/* footer */
.site-footer{left:0;top:2296px;width:1200px;height:280px;background:var(--footer)}
.footer-cols{left:185px;top:2312px;width:840px;display:grid;grid-template-columns:170px 190px 255px 1fr}
.footer-cols h4{color:#fff;font-size:10.5px;font-weight:600;text-transform:uppercase;border-bottom:1px solid #5a5a5a;padding-bottom:6px;margin-bottom:8px;width:150px}
.footer-cols li{color:#ddd;font-size:10.5px;line-height:1.95}
.contact-grid{display:grid;grid-template-columns:70px 1fr;color:#ddd;font-size:10.5px;line-height:1.6}
.newsletter{left:0;top:2576px;width:1200px;height:130px;background:var(--footer-deep);color:#eee;text-align:center}
.newsletter .lead{padding-top:8px;font-size:10.5px}
.signup{display:flex;justify-content:center;align-items:center;gap:10px;margin-top:8px}
.signup strong{font-size:17px;font-weight:600;letter-spacing:1px}
.signup .field{width:215px;height:22px;background:#fff;color:#888;text-align:left;padding:3px 8px;font-size:10px}
.signup .go{background:var(--blue-dark);color:#fff;font-weight:700;font-size:10px;padding:4px 12px}
.follow{display:flex;justify-content:center;align-items:center;gap:6px;margin-top:14px;font-size:9.5px;font-weight:600}
.follow i{width:18px;height:18px;display:inline-block;border-radius:2px}
.copyright{margin-top:16px;font-size:10px}
</style>
</head>
<body>

<!-- header -->
<div class="abs account-bar">
  <a href="#"><svg viewBox="0 0 12 12"><circle cx="6" cy="4" r="3" fill="#fff"/><path d="M0 12c0-4 12-4 12 0z" fill="#fff"/></svg>MY ACCOUNT</a>
</div>
<div class="abs brand"><span class="brand-square"></span><span class="brand-name">BRTL</span></div>
<div class="abs brand-tag">Coastal Linkage Engineering service</div>
<div class="abs phone">
  <svg width="20" height="26" viewBox="0 0 20 26"><path d="M4 1l4 0 1 6-3 2c1 4 3 7 6 9l3-2 4 3-1 5c-10 0-18-11-18-20z" fill="#1d2a38"/></svg>
  1300 555 214
</div>
<div class="abs search"><span>Keywords</span>
  <svg width="11" height="11" viewBox="0 0 11 11"><circle cx="4.5" cy="4.5" r="3.5" stroke="#777" fill="none" stroke-width="1.4"/><path d="M7 7l3.5 3.5" stroke="#777" stroke-width="1.6"/></svg>
</div>

<nav class="abs main-nav">
  <a class="is-active" href="#">Home</a><a href="#">About Us</a><a href="#">Services</a><a href="#">ISP</a><a href="#">Recent Projects</a><a href="#">Blog</a><a href="#">Contact Us</a>
</nav>

<!-- slider -->
<div class="abs hero-band"></div>
<section class="abs hero" role="img" aria-label="Slide photo: technician hands working on a fibre optic splicing machine">
  <div class="abs hero-caption">
    <h1>Lorm ipsum dolor sit amet, consectetur adipiscing</h1>
    <p>Lorem ipsum dolor sit amet, consectetur adipiscing elit, sed diam nonummy eiusmody gravida neque.</p>
  </div>
  <div class="abs hero-arrow" style="left:0"><svg width="10" height="16"><path d="M8 1L2 8l6 7" stroke="#fff" stroke-width="2" fill="none"/></svg></div>
  <div class="abs hero-arrow" style="right:0"><svg width="10" height="16"><path d="M2 1l6 7-6 7" stroke="#fff" stroke-width="2" fill="none"/></svg></div>
  <div class="abs hero-dots"><span class="on"></span><span></span><span></span><span></span><span></span></div>
</section>

<!-- intro columns -->
<section class="abs intro">
  <div class="intro-col">
    <h2><svg width="26" height="18" viewBox="0 0 26 18"><circle cx="8" cy="5" r="4" fill="#8aa"/><circle cx="18" cy="5" r="4" fill="#8aa"/><path d="M0 18c0-7 16-7 16 0zM10 18c0-7 16-7 16 0z" fill="#8aa"/></svg>Who We Are</h2>
    <p>Lorem ipsum dolor sit amet, consectetur adipiscing elit. Sed diam nonummy in convallis gravida neque. Nulla gravida ela tibulum nisle a accumsan, aliquam is sagi llo ut. Sollicitudin sed massa ut enim ve mauri. Curabitur tempus semvitae mi vestibulum volutpat malesu ada erat volutpat malesu ada erat ...</p>
  </div>
  <div class="intro-col">
    <h2><svg width="18" height="20" viewBox="0 0 18 20"><rect x="1" y="1" width="16" height="18" fill="none" stroke="#8aa" stroke-width="2"/><path d="M4 6h10M4 10h10M4 14h7" stroke="#8aa" stroke-width="1.5"/></svg>What We Do</h2>
    <p>Lorem ipsum dolor sit amet, consectetur adipiscing elit. Sed diam nonummy in convallis gravida neque. Nulla gravida ela tibulum nisle a accumsan, aliquam is sagi llo ut. Sollicitudin sed massa ut enim ve mauri. Curabitur tempus semvitae mi vestibulum volutpat malesu ada erat volutpat malesu ada erat ...</p>
  </div>
  <div class="intro-col">
    <h2><svg width="20" height="20" viewBox="0 0 20 20"><path d="M2 18L13 7M7 2l11 11M15 2l3 3-3 3-3-3z" stroke="#8aa" stroke-width="2" fill="none"/></svg>Our Services</h2>
    <ul class="service-list">
      <li>Commercial Security Systems</li>
      <li>Data &amp; Fibre Installations</li>
      <li>Information Communication &amp; Technology</li>
      <li>Electrical Fit Out</li>
    </ul>
  </div>
</section>
<a class="abs btn intro-btn" style="left:263px" href="#">read more</a>
<a class="abs btn intro-btn" style="left:560px" href="#">read more</a>
<a class="abs btn intro-btn" style="left:852px" href="#">read more</a>

<!-- welcome -->
<section class="abs welcome">
  <h2>Wecome to <span>BRTL.com</span></h2>
  <p>Lorem ipsum dolor sit amet, consectetur adipiscing elit. Sed diam nonummy in convallis gravida neque. Nulla gravida vestibulum nisle a accumsan, aliquam in sagitis ut. Sollicitudin sed massa ut enim veniam. Curabitur tempus semvitae mi vestibulum volutpat malesu ada erat volutpat. Sed ornare tellus eleifend. Duis aliquam dolor sit dolor consequat gravida. Fusce tempus tempus feugiat sit amet. Tincidunt id leo. Fusce semper ornare amet. Lorem ipsum dolor sit amet, consectetur adipiscing elit.</p>
  <a class="more" href="#">read more</a>
</section>
<div class="abs welcome-photo" role="img" aria-label="Photo of a business professional in a suit at a modern office"></div>

<!-- project highlights -->
<section class="abs showcase">
  <div class="tabs"><span class="on">FEATURED</span><span>FIBRE OPTICS</span><span>SECURITY</span></div>
  <div class="thumbs">
    <div class="thumb" role="img" aria-label="Fibre optic cabling project photo" style="background:linear-gradient(135deg,#9cc7e0,#3e6f92)"></div>
    <div class="thumb" role="img" aria-label="Network cabling project photo" style="background:linear-gradient(135deg,#c9d7b4,#4f7a4a)"></div>
    <div class="thumb" role="img" aria-label="Security camera installation photo" style="background:linear-gradient(135deg,#d3d9df,#6d7a86)"></div>
    <div class="thumb" role="img" aria-label="Technology circuit graphic" style="background:linear-gradient(135deg,#6fc3ee,#1b4f8f)"></div>
    <div class="thumb" role="img" aria-label="Data centre server photo" style="background:linear-gradient(135deg,#a7b6c4,#2a3a4c)"></div>
    <div class="thumb" role="img" aria-label="Office technology photo" style="background:linear-gradient(135deg,#d8dde2,#7c8c9a)"></div>
  </div>
</section>

<!-- about -->
<section class="abs about">
  <h2>ABOUT US</h2>
  <p>Lorem ipsum dolor sit amet, consectetuer adipiscingelit. Sed diam nonummy in convallis gravida neque. Nulla gravida vestibulum nisle a accumsan, aliquam in sagitis ut. Sollicitudin sed massa ut enim veniam. Curabitur tempus semvitae mi vestibulum volutpat malesu ada erat vestibulum.</p>
  <p>Lorem ipsum dolor sit amet, consectetuer adipiscingelit. Sed diam nonummy in convallis gravida neque. Nulla gravida vestibulum nisle a accumsan, aliquam in sagitis ut. Sollicitudin sed massa ut enim veniam. Curabitur tempus semvitae mi vestibulum volutpat malesu ada erat vestibulum.</p>
  <p>Lorem ipsum dolor sit amet, consectetuer adipiscingelit. Sed diam nonummy in convallis gravida neque. Nulla gravida vestibulum nisle a accumsan, aliquam in sagitis ut. Sollicitudin sed massa ut enim veniam. Curabitur tempus semvitae volutpat malesuada erat vestibulum.</p>
</section>
<a class="abs btn about-btn" href="#">read more</a>

<section class="abs news">
  <h3>Latest News &amp; Events</h3>
  <div class="news-item"><div class="news-thumb" role="img" aria-label="News photo" style="background:linear-gradient(#9fc2d8,#456c88)"></div><div><b>Lorem ipsum dolor sit amet, consectetur adipiscing elit.</b><em>January 12th, 2015</em><p>Lorem ipsum dolor sit amet, consectetur adipiscing elit, sed diam nonu my eiusmoda gravida neque.</p></div></div>
  <div class="news-item"><div class="news-thumb" role="img" aria-label="News photo" style="background:linear-gradient(#c8ccd2,#6b7580)"></div><div><b>Lorem ipsum dolor sit amet, consectetur adipiscing elit.</b><em>January 28th, 2015</em><p>Lorem ipsum dolor sit amet, consectetur adipiscing elit, sed diam nonu my eiusmoda gravida neque.</p></div></div>
  <div class="news-item"><div class="news-thumb" role="img" aria-label="News photo" style="background:linear-gradient(#7fb7dc,#24557d)"></div><div><b>Lorem ipsum dolor sit amet, consectetur adipiscing elit.</b><em>February 10th, 2015</em><p>Lorem ipsum dolor sit amet, consectetur adipiscing elit, sed diam nonu my eiusmoda gravida neque.</p></div></div>
  <div class="news-item"><div class="news-thumb" role="img" aria-label="News photo" style="background:linear-gradient(#d5c9b8,#7a6a58)"></div><div><b>Lorem ipsum dolor sit amet, consectetur adipiscing elit.</b><em>March 11th, 2015</em><p>Lorem ipsum dolor sit amet, consectetur adipiscing elit, sed diam nonu my eiusmoda gravida neque.</p></div></div>
  <a class="view-all" href="#">View All</a>
</section>

<!-- partners -->
<section class="abs partners">
  <h2>Our Partners</h2>
  <p>Lorem ipsum dolor sit amet, consectetur adipiscing elit. Sed diam nonummy incomvallis gravida neque.</p>
  <div class="partner-row">
    <div class="partner-badge"></div>
    <div class="partner-badge round"></div>
    <div class="partner-badge"></div>
    <div class="partner-badge"></div>
    <div class="partner-badge"></div>
  </div>
</section>

<!-- testimonials -->
<h2 class="abs reviews-title">What Our Customer Says</h2>
<section class="abs reviews">
  <div class="review"><div class="avatar" role="img" aria-label="Customer portrait"></div><div><p>Lorem ipsum dolor sit amet, consectetur adipiscing elit. Sed diam nonummy incomvallis gravida neque. Nulla gravida vestibulum nisle a accumsan aliquam in sagittisut.</p><cite><b>Mia Carlton</b>, Marketing , Bristol</cite></div></div>
  <div class="review"><div class="avatar" role="img" aria-label="Customer portrait"></div><div><p>Lorem ipsum dolor sit amet, consectetur adipiscing elit. Sed diam nonummy incomvallis gravida neque. Nulla gravida vestibulum nisle a accumsan aliquam in sagittisut.</p><cite><b>Owen Hartley</b>, IT Engineer, Washington</cite></div></div>
  <div class="review"><div class="avatar" role="img" aria-label="Customer portrait"></div><div><p>Lorem ipsum dolor sit amet, consectetur adipiscing elit. Sed diam nonummy incomvallis gravida neque. Nulla gravida vestibulum nisle a accumsan aliquam in sagittisut.</p><cite><b>Liam Foster</b> , Public Relations , New York</cite></div></div>
  <div class="review"><div class="avatar" role="img" aria-label="Customer portrait"></div><div><p>Lorem ipsum dolor sit amet, consectetur adipiscing elit. Sed diam nonummy incomvallis gravida neque. Nulla gravida vestibulum nisle a accumsan aliquam in sagittisut.</p><cite><b>Noah Pritchard</b>, CEO, Marketing , Washington</cite></div></div>
</section>

<!-- footer -->
<footer class="abs site-footer"></footer>
<div class="abs footer-cols">
  <div><h4>Main Menu</h4><ul><li>Home</li><li>About Us</li><li>Services</li><li>ISP</li><li>Recent Projects</li><li>Blog</li><li>Contact Us</li></ul></div>
  <div><h4>Usefull Links</h4><ul><li>Terms &amp; Conditions</li><li>Privacy policy</li><li>HELP</li><li>FAQ's</li><li>Sitemap</li></ul></div>
  <div><h4>Get In Touch</h4>
    <ul><li>BRTL, Inc.</li></ul>
    <div class="contact-grid" style="margin-bottom:10px"><span style="grid-column:1/3">Lorem Ipsum 4987<br>987786, Melbourne, Australia</span></div>
    <div class="contact-grid"><span>Telephone</span><span>(03) 9555 0142</span><span>Fax</span><span>(03) 9555 0143</span><span>E-mail</span><span>info@brtl.com.au</span></div>
  </div>
  <div><h4>My Account</h4><ul><li>My Account</li><li>Sign In</li><li>Service Requests</li><li>Documents</li><li>Support</li></ul></div>
</div>
<section class="abs newsletter">
  <p class="lead">Receive Our News &amp; updates weekly, no worry about your details</p>
  <div class="signup"><strong>NEWSLETTER</strong><span class="field">Your email address</span><span class="go">SUBMIT</span></div>
  <div class="follow">FOLLOW US ON
    <i style="background:#3b5a9a"></i><i style="background:#29a9e1"></i><i style="background:#0e76a8"></i><i style="background:#d23e2b"></i><i style="background:#7a7a7a"></i><i style="background:#f08a24"></i>
  </div>
  <p class="copyright">Copyright © 2014 BRTL.com. All right reserved.</p>
</section>

</body>
</html>
```